LURN Tax
Ledger Upkeep and Revenue Navigators
Project: LURN Tax
LURN Tax  - Financial Services
Creative Brief
Professional
Milton Prask, CPA CGA
President & CEO
47 Tolland Crescent Suite 2210 Harbourvale Court Dartmouth, NS B2K 7P1
mhp@lurn-example.ca
www.lurn-example.ca

```html
<!DOCTYPE html>
<html lang="en">
<head>
<meta charset="utf-8">
<title>LURN Tax – Stationery</title>
<link rel="stylesheet" href="https://fonts.googleapis.com/css2?family=Cinzel:wght@700&family=Open+Sans:wght@400;600&display=swap">
<style>
  :root{
    --bg:#e4e4e4;
    --paper:#ffffff;
    --navy:#16306f;
    --blue:#2f6fd1;
    --ink:#4a4f5a;
    --soft:#9aa0aa;
  }
  *{box-sizing:border-box;margin:0;padding:0}
  html,body{width:1200px;height:937px;overflow:hidden;background:var(--bg)}
  .canvas{position:relative;width:1200px;height:937px}
  .sheet{position:absolute;background:var(--paper);overflow:hidden}
  .wave{position:absolute;left:0;bottom:0;width:100%}
  .brand{display:flex;align-items:center;gap:8px;color:var(--navy)}
  .brand-mark{background:var(--navy);flex:none}
  .brand-name{font-family:"Cinzel",serif;font-weight:700;color:var(--navy);white-space:nowrap;line-height:1}
  .tagline{font-family:"Cinzel",serif;font-weight:700;color:var(--navy);white-space:nowrap}
  .small{font-family:"Open Sans",sans-serif;color:var(--ink);font-size:6.5px;line-height:1.55}

  /* letterhead */
  .letterhead{left:185px;top:106px;width:385px;height:500px}
  .letterhead .brand{position:absolute;left:26px;top:30px}
  .letterhead .brand-mark{width:14px;height:14px}
  .letterhead .brand-name{font-size:19px}
  .letter-contact{position:absolute;right:26px;top:30px;text-align:right}
  .letter-body{position:absolute;left:26px;top:92px;width:330px}
  .letter-body p{margin-bottom:9px}
  .signature{width:46px;height:16px;background:#e8ebf2;margin:4px 0 6px}
  .letter-footer{position:absolute;left:26px;top:408px;color:var(--soft)}

  /* folder */
  .folder{left:633px;top:106px;width:460px;height:500px}
  .folder-lockup{position:absolute;left:0;right:0;top:180px;display:flex;flex-direction:column;align-items:center;gap:12px}
  .folder .brand-mark{width:24px;height:24px}
  .folder .brand-name{font-size:42px}
  .folder .tagline{font-size:11.5px;letter-spacing:.3px}

  /* business cards */
  .card{left:43px;width:202px;height:96px}
  .card-front{top:670px}
  .card-back{top:784px}
  .card .brand{position:absolute;left:16px;top:18px;gap:5px}
  .card .brand-mark{width:8px;height:8px}
  .card .brand-name{font-size:12px}
  .card-front .tagline{position:absolute;left:16px;top:36px;font-size:4.6px}
  .card-back .brand{top:16px}
  .card-contact{position:absolute;right:14px;top:14px;text-align:right;font-size:5px}

  /* envelopes */
  .envelope{top:678px;height:202px}
  .envelope-front{left:266px;width:430px}
  .envelope-front .brand{position:absolute;left:24px;top:24px}
  .envelope-front .brand-mark{width:12px;height:12px}
  .envelope-front .brand-name{font-size:19px}
  .envelope-front .tagline{position:absolute;left:24px;top:48px;font-size:6.5px}
  .envelope-back{left:739px;width:425px;background:var(--paper)}
  .envelope-flap{position:absolute;left:0;top:0;width:100%;height:86px}
  .envelope-url{position:absolute;right:22px;top:18px;font-family:"Open Sans",sans-serif;font-size:9px;letter-spacing:1px;color:#fff}
</style>
</head>
<body>
<main class="canvas">

  <!-- Letterhead -->
  <section class="sheet letterhead">
    <div class="brand"><span class="brand-mark"></span><span class="brand-name">LURN Tax</span></div>
    <div class="letter-contact small">
      <div>Milton Prask</div>
      <div>(902) 555-0147</div>
      <div>mhp@lurn-example.ca</div>
    </div>
    <div class="letter-body small">
      <p>July 4, 2024<br>Client Name<br>123 Sample Street, City</p>
      <p>Thank you for choosing our firm for your tax and advisory needs. This letter confirms the scope of our work for the coming year and the documents we will need from you.</p>
      <p>Please send your records before the end of the month so we can prepare your returns on time.</p>
      <p>We look forward to working with you. If you have any questions, our team is always glad to help you plan for growth.</p>
      <p>Sincerely,</p>
      <div class="signature" role="img" aria-label="Handwritten signature"></div>
      <p>Milton Prask<br>President &amp; CEO</p>
    </div>
    <div class="letter-footer small">47 Tolland Crescent Suite 2210 Harbourvale Court, Dartmouth, NS B2K 7P1</div>
    <svg class="wave" viewBox="0 0 385 80" height="80" preserveAspectRatio="none" aria-hidden="true">
      <path d="M0 38 Q190 8 385 30" fill="none" stroke="var(--blue)" stroke-width="2"/>
      <path d="M0 50 Q190 14 385 40 L385 80 L0 80 Z" fill="var(--navy)"/>
    </svg>
  </section>

  <!-- Presentation folder -->
  <section class="sheet folder">
    <div class="folder-lockup">
      <div class="brand"><span class="brand-mark"></span><span class="brand-name">LURN Tax</span></div>
      <div class="tagline">Ledger Upkeep and Revenue Navigators</div>
    </div>
    <svg class="wave" viewBox="0 0 460 90" height="90" preserveAspectRatio="none" aria-hidden="true">
      <path d="M0 44 Q230 10 460 34" fill="none" stroke="var(--blue)" stroke-width="2"/>
      <path d="M0 56 Q230 16 460 44 L460 90 L0 90 Z" fill="var(--navy)"/>
    </svg>
  </section>

  <!-- Business card front -->
  <section class="sheet card card-front">
    <div class="brand"><span class="brand-mark"></span><span class="brand-name">LURN Tax</span></div>
    <div class="tagline">Ledger Upkeep and Revenue Navigators</div>
    <svg class="wave" viewBox="0 0 202 34" height="34" preserveAspectRatio="none" aria-hidden="true">
      <path d="M0 14 Q100 2 202 12" fill="none" stroke="var(--blue)" stroke-width="1.2"/>
      <path d="M0 20 Q100 6 202 16 L202 34 L0 34 Z" fill="var(--navy)"/>
    </svg>
  </section>

  <!-- Business card back -->
  <section class="sheet card card-back">
    <div class="brand"><span class="brand-mark"></span><span class="brand-name">LURN Tax</span></div>
    <div class="card-contact small">
      <div>Milton Prask, CPA CGA</div>
      <div>President &amp; CEO</div>
      <div>mhp@lurn-example.ca</div>
      <div>www.lurn-example.ca</div>
    </div>
    <svg class="wave" viewBox="0 0 202 30" height="30" preserveAspectRatio="none" aria-hidden="true">
      <path d="M0 12 Q100 2 202 10" fill="none" stroke="var(--blue)" stroke-width="1.2"/>
      <path d="M0 18 Q100 6 202 14 L202 30 L0 30 Z" fill="var(--navy)"/>
    </svg>
  </section>

  <!-- Envelope front -->
  <section class="sheet envelope envelope-front">
    <div class="brand"><span class="brand-mark"></span><span class="brand-name">LURN Tax</span></div>
    <div class="tagline">Ledger Upkeep and Revenue Navigators</div>
    <svg class="wave" viewBox="0 0 430 64" height="64" preserveAspectRatio="none" aria-hidden="true">
      <path d="M0 28 Q215 4 430 22" fill="none" stroke="var(--blue)" stroke-width="1.6"/>
      <path d="M0 38 Q215 10 430 30 L430 64 L0 64 Z" fill="var(--navy)"/>
    </svg>
  </section>

  <!-- Envelope back -->
  <section class="sheet envelope envelope-back">
    <svg class="envelope-flap" viewBox="0 0 425 86" preserveAspectRatio="none" aria-hidden="true">
      <path d="M0 0 H425 V58 Q212 86 0 66 Z" fill="var(--navy)"/>
      <path d="M0 74 Q212 96 425 66" fill="none" stroke="var(--blue)" stroke-width="1.6"/>
    </svg>
    <div class="envelope-url">www.lurn-example.ca</div>
  </section>

</main>
</body>
</html>
```